Business Card for Multi-Brand Sportswear Company

We are looking for a business card which represents our company and the multiple brands within it.

The company: Fen Athletics (LTD)
The brands: Fen, TavaPuni, ElmStretch, Grit and Rain

Employees using these cards would be representing Fen Athletics, rather than any of the individual brands. You will see a current design within the uploaded files, to give some inspiration. The actual text of the brands is not necessary, but the logos should be on there is some format.

Our creative minds on this are stretched, so we are looking for someone to make this their own, and show us what a good business card should look like.

We may like to get these printed with spot gloss, so keep that in mind with your designs.

www.fenathletics.co.uk

Industry/Entity Type

Business

Contact Information for Business Card

Leo Pemberton-Hale
Operations Manager
(+44) 1632 960 418
Leo@fenathletics.co.uk
www.fenathletics.co.uk

Font styles to use
Sans Serif
Other font styles liked:
• Eurostile

Colors
ffffff

Requirements
Nice to have
• Dark (black) background

```html
<!DOCTYPE html>
<html lang="en">
<head>
<meta charset="utf-8">
<title>Fen Athletics – Business Card</title>
<link href="https://fonts.googleapis.com/css2?family=Open+Sans:wght@400;600;700&display=swap" rel="stylesheet">
<style>
  :root {
    --backdrop: #3a3a3c;
    --card-white: #ffffff;
    --ink: #1a1a1a;
    --accent-red: #e0161e;
    --red-deep: #a50f14;
    --red-light: #e8222a;
    --silver: #d9d9db;
    --brand-purple: #5d4a66;
    --brand-grey: #8f8f8f;
  }
  * { box-sizing: border-box; margin: 0; padding: 0; }
  html, body {
    width: 1200px; height: 900px; overflow: hidden;
    background: var(--backdrop);
    font-family: "Open Sans", Arial, sans-serif;
  }
  .stage {
    position: relative; width: 1200px; height: 900px;
    display: flex; align-items: center; justify-content: center; gap: 60px;
  }
  .card {
    position: relative; width: 525px; height: 300px;
    border-radius: 26px; overflow: hidden;
  }
  .card--front { background: var(--card-white); color: var(--ink); }
  .card--back {
    background: radial-gradient(ellipse at 50% 45%, var(--red-light) 0%, var(--red-deep) 100%);
    display: flex; align-items: center; justify-content: center;
  }
  .contact {
    position: absolute; top: 30px; right: 30px;
    list-style: none; text-align: right; font-size: 12px; line-height: 18px;
  }
  .contact li { display: flex; align-items: center; justify-content: flex-end; gap: 6px; }
  .contact svg { width: 10px; height: 10px; fill: var(--accent-red); }
  .person { position: absolute; top: 92px; left: 32px; }
  .person__name { color: var(--accent-red); font-weight: 700; font-size: 16px; letter-spacing: 0.3px; }
  .person__role { font-size: 13px; margin-top: -2px; }
  .company-name {
    position: absolute; top: 140px; left: 32px;
    font-weight: 600; font-size: 34px; color: var(--ink); letter-spacing: 0.5px;
  }
  .address {
    position: absolute; top: 150px; right: 30px;
    text-align: right; font-size: 12.5px; line-height: 18px;
  }
  .brands {
    position: absolute; left: 32px; bottom: 32px;
    display: flex; gap: 26px; align-items: center; list-style: none;
  }
  .brand { display: flex; align-items: center; gap: 7px; font-size: 12px; font-weight: 600; color: var(--ink); }
  .brand__mark { width: 22px; height: 22px; }
  .brand__mark--square { background: var(--brand-purple); border-radius: 4px; }
  .brand__mark--red { border-radius: 50%; background: var(--accent-red); }
  .brand__mark--circle { border-radius: 50%; border: 2px solid var(--brand-grey); }
  .back-name { font-weight: 600; font-size: 40px; color: var(--silver); letter-spacing: 0.5px; }
</style>
</head>
<body>
<main class="stage">
  <section class="card card--front" aria-label="Card front">
    <ul class="contact">
      <li>+44(0)1632 960418
        <svg viewBox="0 0 10 10"><path d="M2 0.5 L3.6 0.5 L4.2 2.8 L3 3.6 C3.6 5 5 6.4 6.4 7 L7.2 5.8 L9.5 6.4 L9.5 8 C9.5 9 8.8 9.5 8 9.5 C4 9.5 0.5 6 0.5 2 C0.5 1.2 1 0.5 2 0.5Z"/></svg></li>
      <li>leo@fenathletics.co.uk
        <svg viewBox="0 0 10 10"><rect x="0.5" y="2" width="9" height="6.5" rx="1"/><path d="M1 2.5 L5 5.5 L9 2.5" stroke="#fff" stroke-width="0.9" fill="none"/></svg></li>
      <li>www.fenathletics.co.uk
        <svg viewBox="0 0 10 10"><circle cx="5" cy="5" r="4.5"/><path d="M0.5 5 H9.5 M5 0.5 C2.5 3 2.5 7 5 9.5 M5 0.5 C7.5 3 7.5 7 5 9.5" stroke="#fff" stroke-width="0.8" fill="none"/></svg></li>
    </ul>
    <div class="person">
      <p class="person__name">LEO PEMBERTON-HALE</p>
      <p class="person__role">Managing Director</p>
    </div>
    <p class="company-name">Fen Athletics</p>
    <address class="address" style="font-style:normal">Marsh Yard,<br>Elmby, Fenwick, ZZ9 4QT</address>
    <ul class="brands">
      <li class="brand"><span class="brand__mark brand__mark--square"></span>TavaPuni</li>
      <li class="brand"><span class="brand__mark brand__mark--red"></span>Grit and Rain</li>
      <li class="brand"><span class="brand__mark brand__mark--circle"></span>ElmStretch</li>
    </ul>
  </section>
  <section class="card card--back" aria-label="Card back">
    <p class="back-name">Fen Athletics</p>
  </section>
</main>
</body>
</html>
```